Online Greeting Card Marketplace redesign

PennedNotes.com is a two-sided greeting card marketplace. Buyers purchase hand-made cards online, indicating their message. Sellers hand-write the message and mail directly to recipient.

We are getting decent foot traffic but low sales. I'm also not drawing a lot of Card Designers to sell their products. Feedback has been that it's cluttered, boring, and out of date.

I've always enjoyed vibes such as Dana Holloway and Gwen Rutledge. I was going for pale blues and chocolate browns (as can be seen in PennedNotes Chatterly and Flitter pages).

Attached document is my not-so-great attempt to redesign, which is uninviting and unpolished.

Need a new homepage and a second similar page when shopping (click on any category to see what I mean, e.g. Halloween).
Updates

Industry/Entity Type

Shopping

Requirements
Must have
• I think my logo (stick drawing of a man with an envelope) is what is currently driving a lot of traffic and should stay in the design, pending minor tweaks.

I'll need all the details of the final design to give to the programmers (font styles, color numbers, etc).

Nice to have
• I was thinking of a dotted frame to surround each picture? White Pearl luminescent or a metallic? I just don't know if it works.

```html
<!DOCTYPE html>
<html lang="en">
<head>
<meta charset="utf-8">
<title>PennedNotes.com – Halloween</title>
<link href="https://fonts.googleapis.com/css2?family=PT+Sans:wght@400;700&family=PT+Sans+Narrow:wght@400;700&display=swap" rel="stylesheet">
<style>
:root{
  --ink:#444444;
  --link:#2f6fb3;
  --bar:#8e999b;
  --frame:#c4c4c4;
  --footer:#121212;
  --white:#ffffff;
  --muted:#777777;
}
*{box-sizing:border-box;margin:0;padding:0}
html,body{width:939px;height:1200px;overflow:hidden;background:var(--white)}
body{position:relative;font-family:"PT Sans",Arial,sans-serif;color:var(--ink)}
.top-rule{position:absolute;left:0;top:0;width:939px;height:4px;background:#474747}
.utility-nav{position:absolute;top:19px;left:0;width:939px;display:flex;justify-content:center;font-size:12px}
.utility-nav a{color:var(--link);text-decoration:none;padding:0 14px;border-left:1px dotted #b8b8b8;line-height:16px}
.utility-nav a:first-child{border-left:none}
.brand{position:absolute;top:70px;left:0;width:939px;text-align:center}
.brand-name{display:inline-flex;align-items:center;gap:10px;font-size:30px;color:var(--ink)}
.brand-name .mark{width:22px;height:22px;background:var(--link)}
.brand-tagline{font-size:13px;color:var(--muted);margin-top:4px;letter-spacing:.5px}
.cart{position:absolute;top:103px;left:770px;font-size:13px;color:var(--ink);display:flex;align-items:center;gap:6px}
.category-bar{position:absolute;left:68px;top:169px;width:803px;height:42px;background:var(--bar);display:flex;align-items:center;padding-left:17px;font-family:"PT Sans Narrow",Arial,sans-serif;font-size:16px;color:var(--white)}
.category-bar span{margin-right:41px}
.search{position:absolute;right:9px;top:7px;width:176px;height:27px;background:var(--white);border-radius:3px;font-family:"PT Sans",Arial,sans-serif;font-size:11px;font-style:italic;color:#999;padding:6px 9px}
.search svg{position:absolute;right:9px;top:7px}
.breadcrumb{position:absolute;left:70px;top:232px;font-family:"PT Sans Narrow",Arial,sans-serif;font-size:16px;color:var(--link)}
.breadcrumb i{font-style:normal;margin:0 7px}
.section-title{position:absolute;left:0;width:939px;text-align:center;font-family:"PT Sans Narrow",Arial,sans-serif;font-size:19px;color:var(--ink)}
.card-row{position:absolute;left:106px;display:grid;grid-template-columns:repeat(4,173px);gap:10px}
.card{height:221px;border:1px dotted var(--frame);padding:6px}
.card .art{width:159px;height:143px}
.card .sku{margin-top:14px;font-size:12.5px;color:var(--link)}
.card .price{margin-top:6px;font-size:14.5px;font-weight:700;color:#555}
.slider-arrow{position:absolute;top:380px}
.pagination{position:absolute;left:106px;top:1075px;display:flex;gap:8px;font-size:11px}
.pagination span{border:1px solid #ccc;background:#f1f1f1;height:20px;min-width:18px;padding:0 5px;line-height:18px;text-align:center;color:var(--ink)}
.site-footer{position:absolute;left:0;top:1119px;width:939px;height:81px;background:var(--footer);color:var(--white);font-size:11.5px}
.footer-links{position:absolute;left:68px;top:22px}
.copyright{position:absolute;left:68px;top:48px}
.social{position:absolute;right:68px;top:27px;display:flex;gap:14px}
.social span{display:flex;align-items:center;gap:4px;font-size:11px}
.social i{width:12px;height:12px;display:block}
</style>
</head>
<body>
<div class="top-rule"></div>

<nav class="utility-nav">
  <a>HOME</a><a>HOW IT WORKS</a><a>SELL</a><a>CREATE AN ACCOUNT</a><a>CHECK OUT</a><a>LOGIN</a>
</nav>

<header class="brand">
  <div class="brand-name"><span class="mark"></span>PennedNotes.com</div>
  <div class="brand-tagline">Hand-Made. Hand-Written. Hand-Delivered</div>
</header>

<div class="cart">
  <svg width="16" height="14" viewBox="0 0 16 14"><path d="M1 1h3l2 8h8l1-6H5" fill="none" stroke="#666" stroke-width="1.3"/><circle cx="7" cy="12" r="1.3" fill="#666"/><circle cx="13" cy="12" r="1.3" fill="#666"/></svg>
  Cart (0) items
</div>

<div class="category-bar">
  <span>UPCOMING HOLIDAYS</span><span>EVERYDAY CARDS</span><span>BIRTHDAYS</span><span>ALL CATEGORIES</span>
  <div class="search">Search..
    <svg width="12" height="12" viewBox="0 0 12 12"><circle cx="5" cy="5" r="3.8" fill="none" stroke="#999" stroke-width="1.5"/><path d="M8 8l3 3" stroke="#999" stroke-width="1.5"/></svg>
  </div>
</div>

<div class="breadcrumb">HOME<i>::</i>HALLOWEEN<i>::</i>CAT SILHOUETTE</div>

<h2 class="section-title" style="top:268px">BEST SELLING CARDS</h2>

<svg class="slider-arrow" style="left:76px" width="16" height="48" viewBox="0 0 16 48"><path d="M14 2L3 24l11 22" fill="none" stroke="#999" stroke-width="2"/></svg>
<svg class="slider-arrow" style="left:846px" width="16" height="48" viewBox="0 0 16 48"><path d="M2 2l11 22L2 46" fill="none" stroke="#999" stroke-width="2"/></svg>

<div class="card-row" style="top:305px">
  <div class="card"><div class="art" role="img" aria-label="Photo of an orange pumpkin" style="background:linear-gradient(160deg,#6b5a2a,#e07a1c 55%,#c95f10)"></div><div class="sku">CARD NUMBER: SKU17597</div><div class="price">$. 6.50</div></div>
  <div class="card"><div class="art" role="img" aria-label="Papercut sailboat card in pale blue" style="background:linear-gradient(180deg,#a9cde8 60%,#1e1e1e)"></div><div class="sku">CARD NUMBER: SKU17597</div><div class="price">$. 6.50</div></div>
  <div class="card"><div class="art" role="img" aria-label="Photo of a dog with a toy truck before a flag" style="background:linear-gradient(180deg,#b33a3a,#d9d9e6 40%,#5a5a4f)"></div><div class="sku">CARD NUMBER: SKU17597</div><div class="price">$. 3.50</div></div>
  <div class="card"><div class="art" role="img" aria-label="Halloween monster figure beside a pumpkin" style="background:linear-gradient(135deg,#3e5a3a,#4a4a8a 50%,#d26a1f)"></div><div class="sku">CARD NUMBER: SKU17597</div><div class="price">$. 7.00</div></div>
</div>

<h2 class="section-title" style="top:551px">HALLOWEEN</h2>

<div class="card-row" style="top:589px">
  <div class="card"><div class="art" role="img" aria-label="Colourful birthday balloons illustration" style="background:linear-gradient(180deg,#bfe3ef,#f3c64a 55%,#e36a8a)"></div><div class="sku">CARD NUMBER: SKU17597</div><div class="price">$ 7.68</div></div>
  <div class="card"><div class="art" role="img" aria-label="Ferris wheel card with a couple" style="background:linear-gradient(180deg,#d8cbbd,#efe9e2)"></div><div class="sku">CARD NUMBER: SKU17597</div><div class="price">$ 4.00</div></div>
  <div class="card"><div class="art" role="img" aria-label="Floral sympathy card on red" style="background:linear-gradient(180deg,#8e2a2a 8%,#f2e6cf 12%,#efe2c8 70%,#6b4038 80%,#8e2a2a)"></div><div class="sku">CARD NUMBER: SKU17597</div><div class="price">$ 4.85</div></div>
  <div class="card"><div class="art" role="img" aria-label="New baby boy congratulations card" style="background:linear-gradient(135deg,#5cc6c9,#ffffff 45%,#f3d56a)"></div><div class="sku">CARD NUMBER: SKU17597</div><div class="price">$ 6.50</div></div>
</div>

<div class="card-row" style="top:834px">
  <div class="card"><div class="art" role="img" aria-label="Halloween night scene with a witch and haunted house" style="background:linear-gradient(180deg,#1f2a3a 45%,#e8782a 70%,#2a1c14)"></div><div class="sku">CARD NUMBER: SKU17597</div><div class="price">$ 3.50</div></div>
  <div class="card"><div class="art" role="img" aria-label="Row of jack-o-lanterns with Happy Halloween lettering" style="background:linear-gradient(180deg,#e8641c 65%,#f3c34a)"></div><div class="sku">CARD NUMBER: SKU17597</div><div class="price">$ 9.50</div></div>
  <div class="card"><div class="art" role="img" aria-label="Happy Halloween hand-lettered sign with a pumpkin" style="background:linear-gradient(135deg,#e3b23a,#3e6a34 50%,#d98a2a)"></div><div class="sku">CARD NUMBER: SKU17597</div><div class="price">$ 3.50</div></div>
  <div class="card"><div class="art" role="img" aria-label="Gone trick or treating card with spider web" style="background:linear-gradient(135deg,#e07a2a,#f4c25c 60%,#3a2a20)"></div><div class="sku">CARD NUMBER: SKU17597</div><div class="price">$ 9.50</div></div>
</div>

<div class="pagination">
  <span>PREV</span><span>1</span><span>2</span><span>3</span><span>4</span><span>5</span><span>6</span><span>....</span><span>NEXT</span>
</div>

<footer class="site-footer">
  <div class="footer-links">About us | FAQ | Contact us</div>
  <div class="copyright">Copyrights 2013. All Rights Reserved.</div>
  <div class="social">
    <span><i style="background:#3b5aa8"></i>Chatterly</span>
    <span><i style="background:#2a9ad6"></i>Flitter</span>
    <span><i style="background:#f07a1a"></i>Feed</span>
    <span><i style="background:#d82a2a"></i>Vidstream</span>
  </div>
</footer>
</body>
</html>
```